New, modern business card for growing audiology practice

We need a new business card for our audiology practice. Our logo and website have recently changed (more modern) and we want our business cards to reflect this change.
We conduct hearing tests, perform earwax removals, and fit & dispense hearing aids to our patients. We are a family owned practice in which the owner is the one who works directly with the patient. I have attached logos in various formats to use, as well as two ideas I found on this website; as well as a scanned copy of our current logo. Good luck!

Industry/Entity Type

Business

Contact Information for Business Card

Company name: Tolvera Hearing Center
Provider name: Peter Wolstenby, Au.D. F/NSB
Phone number: (440) 683-5127
Address: 837 W. Lindell Ave. Brenmoor Falls, OH 44931
email: tolverahearing@postvane.com
website: tolverahearing.com

Colors
000000
aaaaaa
dbdbdb
cacaca
9bcb3c
afd23c
cadf82
b1b1b1

Requirements
Must have
• My card must include information in the "details" section. In the attached images, I found a few that I liked and I would like to model after - "brisky bouncin'" and "Sound Method Center".
• Must be horizontal.
• Must include logos provided. I uploaded them in various file formats and various ways.
• Must match logo font, if possible, if not, please get as close as you can.
Nice to have
• I really like the idea of having a color on one side with just the logo and company name and the contact information and provider name on the other side. I also really like the idea of having the main color dominating on the logo/company side with accent of that same color on the contact side of the card.
Should not have
• Must not be vertical.

```html
<!DOCTYPE html>
<html lang="en">
<head>
<meta charset="utf-8">
<title>Tolvera Hearing Center – Business Card</title>
<link rel="stylesheet" href="https://fonts.googleapis.com/css2?family=Lato:wght@400&family=Roboto:wght@400;500&display=swap">
<style>
  :root {
    --backdrop: #e9e9e6;
    --card-white: #f4f4f4;
    --brand-green: #6f9c34;
    --ink: #111111;
    --text-grey: #555555;
    --rule-grey: #b1b1b1;
    --white: #ffffff;
  }
  * { margin: 0; padding: 0; box-sizing: border-box; }
  html, body {
    width: 1200px; height: 960px; overflow: hidden;
    background: var(--backdrop);
  }
  .canvas { position: relative; width: 1200px; height: 960px; }

  .card {
    position: absolute; width: 600px; height: 342px;
    box-shadow: 0 2px 6px rgba(0,0,0,0.25);
  }

  /* Contact side */
  .card--contact { left: 314px; top: 113px; background: var(--card-white); }
  .brand {
    position: absolute; display: flex; align-items: center; gap: 8px;
    font-family: "Lato", sans-serif; font-weight: 400; letter-spacing: 0.2px;
    white-space: nowrap;
  }
  .brand__dot { width: 12px; height: 12px; border-radius: 50%; flex: none; }
  .card--contact .brand { left: 48px; top: 161px; font-size: 17px; color: var(--ink); }
  .card--contact .brand__dot { background: var(--brand-green); }

  .divider {
    position: absolute; left: 320px; top: 85px; width: 1px; height: 178px;
    background: var(--rule-grey);
  }
  .details {
    position: absolute; left: 351px; top: 90px;
    font-family: "Roboto", sans-serif; color: var(--text-grey);
  }
  .details__name {
    font-size: 20px; font-weight: 500; color: var(--brand-green);
    text-transform: uppercase; line-height: 24px;
  }
  .details__title {
    font-size: 15px; font-weight: 500; color: var(--ink); line-height: 20px; margin-bottom: 11px;
  }
  .details__address { font-size: 14px; line-height: 19px; margin-bottom: 9px; }
  .details__list { list-style: none; font-size: 14px; line-height: 19px; }
  .details__list li { display: flex; align-items: center; gap: 9px; }
  .details__list svg { width: 13px; height: 13px; fill: var(--brand-green); flex: none; }

  .accent-band {
    position: absolute; left: 0; bottom: 0; width: 100%; height: 15px;
    display: flex; gap: 2px; background: var(--white);
  }
  .accent-band span { flex: 1; }
  .accent-band .is-green { background: var(--brand-green); }
  .accent-band .is-black { background: var(--ink); }

  /* Brand side */
  .card--brand { left: 311px; top: 472px; height: 343px; background: var(--brand-green); }
  .card--brand .brand {
    left: 0; right: 0; justify-content: center; top: 155px;
    font-size: 29px; color: var(--white); gap: 12px;
  }
  .card--brand .brand__dot { background: var(--white); width: 16px; height: 16px; }
  .card--brand .site {
    position: absolute; left: 0; right: 0; top: 286px; text-align: center;
    font-family: "Roboto", sans-serif; font-size: 14px; letter-spacing: 3.6px;
    color: var(--white);
  }
</style>
</head>
<body>
<main class="canvas">
  <section class="card card--contact">
    <div class="brand"><span class="brand__dot"></span>TOLVERA HEARING CENTER</div>
    <div class="divider"></div>
    <div class="details">
      <p class="details__name">Peter Wolstenby</p>
      <p class="details__title">AU.D. F/NSB</p>
      <p class="details__address">837 W. Lindell Ave.<br>Brenmoor Falls, OH 44931</p>
      <ul class="details__list">
        <li>
          <svg viewBox="0 0 24 24" aria-hidden="true"><path d="M6.6 10.8a15.1 15.1 0 0 0 6.6 6.6l2.2-2.2c.3-.3.7-.4 1-.2 1.1.4 2.3.6 3.6.6.6 0 1 .4 1 1V20c0 .6-.4 1-1 1A17 17 0 0 1 3 4c0-.6.4-1 1-1h3.5c.6 0 1 .4 1 1 0 1.3.2 2.5.6 3.6.1.3 0 .7-.2 1z"/></svg>
          (440) 683-5127
        </li>
        <li>
          <svg viewBox="0 0 24 24" aria-hidden="true"><path d="M2 6l10 6 10-6v13H2z M2 5h20l-10 6z"/></svg>
          tolverahearing@postvane.com
        </li>
        <li>
          <svg viewBox="0 0 24 24" aria-hidden="true"><circle cx="12" cy="12" r="10"/><path d="M2 12h20M12 2c3 3 3 17 0 20M12 2c-3 3-3 17 0 20" stroke="#f4f4f4" stroke-width="1.5" fill="none"/></svg>
          tolverahearing.com
        </li>
      </ul>
    </div>
    <div class="accent-band">
      <span class="is-green"></span><span class="is-black"></span><span class="is-green"></span><span class="is-black"></span>
    </div>
  </section>

  <section class="card card--brand">
    <div class="brand"><span class="brand__dot"></span>TOLVERA HEARING CENTER</div>
    <p class="site">www.tolverahearing.com</p>
  </section>
</main>
</body>
</html>
```